Movie Poster - Beneath Pale Iron Skies

Documentary-film poster design.
Attached is a PDF brief with information on what is required and examples of poster designs I like.

The project is a true crime / mystery documentary film. Set in the Soviet Union in 1959.

Colors
3276b5
85abd2
ec1f27

```html
<!DOCTYPE html>
<html lang="en">
<head>
<meta charset="utf-8">
<title>Beneath Pale Iron Skies — Documentary Poster</title>
<link href="https://fonts.googleapis.com/css2?family=Big+Shoulders+Stencil+Display:wght@900&family=Montserrat:wght@300;400&display=swap" rel="stylesheet">
<style>
  :root {
    --blue: #3276b5;
    --blue-deep: #1f5aa3;
    --blue-light: #85abd2;
    --red: #ec1f27;
    --white: #ffffff;
    --ink: #111111;
    --mist: #fbeeee;
  }
  html, body {
    margin: 0;
    padding: 0;
    width: 927px;
    height: 1200px;
    overflow: hidden;
    background: var(--blue);
  }
  .poster {
    position: relative;
    width: 927px;
    height: 1200px;
    overflow: hidden;
    background: linear-gradient(180deg, var(--blue-deep) 0%, var(--blue) 55%, #3a7fbf 100%);
    font-family: "Montserrat", sans-serif;
  }
  .poster__atmosphere {
    position: absolute;
    inset: 0;
  }
  .title {
    position: absolute;
    left: 0;
    width: 927px;
    text-align: center;
    margin: 0;
  }
  .title__kicker {
    top: 278px;
    font-family: "Montserrat", sans-serif;
    font-weight: 400;
    font-size: 48px;
    letter-spacing: 1px;
    color: var(--red);
    line-height: 1;
  }
  .title__main {
    top: 342px;
    font-family: "Big Shoulders Stencil Display", sans-serif;
    font-weight: 900;
    font-size: 128px;
    line-height: 1;
    letter-spacing: 2px;
    color: var(--ink);
    z-index: 2;
  }
  .subtitle {
    position: absolute;
    top: 742px;
    left: 0;
    width: 927px;
    text-align: center;
    margin: 0;
    font-weight: 300;
    font-size: 24px;
    color: var(--ink);
    letter-spacing: 0.5px;
  }
  .subtitle__event { color: var(--white); }
  .taglines {
    position: absolute;
    top: 828px;
    left: 0;
    width: 927px;
    text-align: center;
    margin: 0;
    padding: 0;
    list-style: none;
    font-weight: 300;
    font-size: 16px;
    line-height: 27.5px;
    color: var(--white);
    letter-spacing: 0.5px;
  }
</style>
</head>
<body>
<main class="poster">
  <svg class="poster__atmosphere" width="927" height="1200" viewBox="0 0 927 1200" xmlns="http://www.w3.org/2000/svg">
    <defs>
      <filter id="soft-glow" x="-30%" y="-30%" width="160%" height="160%">
        <feGaussianBlur stdDeviation="28"/>
      </filter>
      <linearGradient id="photo-tone" x1="0" y1="0" x2="1" y2="0">
        <stop offset="0" stop-color="#e83a3f"/>
        <stop offset="0.3" stop-color="#f7c9c9"/>
        <stop offset="0.5" stop-color="#ec3b40"/>
        <stop offset="0.75" stop-color="#f06a6d"/>
        <stop offset="1" stop-color="#ec1f27"/>
      </linearGradient>
      <linearGradient id="photo-fade" x1="0" y1="0" x2="0" y2="1">
        <stop offset="0" stop-color="#ffffff" stop-opacity="0.85"/>
        <stop offset="0.35" stop-color="#ffffff" stop-opacity="0"/>
      </linearGradient>
    </defs>

    <g class="glow" filter="url(#soft-glow)" fill="#ffffff">
      <path d="M250 40 C420 0 760 0 860 30 C880 120 760 230 620 300 C520 360 300 420 150 470 C100 360 130 120 250 40 Z" opacity="0.9"/>
      <path d="M120 480 C300 420 640 430 860 480 C900 600 860 720 780 760 C600 800 300 820 140 780 C80 700 80 560 120 480 Z" opacity="0.95"/>
    </g>
    <rect x="0" y="940" width="927" height="260" fill="#3a7fbf" opacity="0.5"/>

    <path class="brush-band" d="M0 458 L80 452 L110 446 L300 440 L520 432 L700 424 L927 414 L927 712 L760 714 L600 720 L420 726 L200 724 L90 720 L0 710 Z" fill="var(--mist)"/>

    <g role="img" aria-label="Red-tinted archival photograph of a group of hooded hikers with ski poles and backpacks in deep snow">
      <path d="M0 470 L60 462 L120 468 L330 476 L560 470 L760 460 L927 455 L927 715 L760 712 L600 720 L430 727 L230 724 L95 722 L0 708 Z" fill="url(#photo-tone)" opacity="0.85"/>
      <path d="M0 470 L927 455 L927 715 L0 708 Z" fill="url(#photo-fade)"/>
    </g>
  </svg>

  <h1 class="title title__kicker">BENEATH</h1>
  <h1 class="title title__main">PALE IRON SKIES</h1>

  <p class="subtitle">The true story of the <span class="subtitle__event">Vorsk Pass Incident</span></p>

  <ul class="taglines">
    <li>Nine dead hikers</li>
    <li>Sixty years of secrets</li>
    <li>Russia’s greatest mystery uncovered.</li>
  </ul>
</main>
</body>
</html>
```